business card

Business card for new business.
Red and black corporate colors.
Card can have an Indsutrial feel to it. Feel free to add Rust, Bolted steel, or graphics as you see fit. We provide highly specialized services to the below mentioned industries.
Keep information out of corners so that if I want I can choose rounded corners.
Information
- front. name - title - phone - email
- Rear
Pipelines - Ports - Utilities - Forestry - Power
Northbridge - Alder Falls - Kestrel Bay - Pinehaven - Stonemere

```html
<!DOCTYPE html>
<html lang="en">
<head>
<meta charset="utf-8">
<title>Girderline Business Card</title>
<link href="https://fonts.googleapis.com/css2?family=Open+Sans:wght@400;600;700;800&display=swap" rel="stylesheet">
<style>
  :root {
    --page-bg: #e6e4e2;
    --card-black: #161616;
    --card-edge: #0c0c0c;
    --brand-red: #e0202c;
    --text-white: #f2f2f2;
    --text-grey: #c9c9c9;
    --rule-grey: #8a8a8a;
    --name-grey: #b8b8b8;
  }
  * { margin: 0; padding: 0; box-sizing: border-box; }
  html, body {
    width: 1200px; height: 864px; overflow: hidden;
    background: var(--page-bg);
    font-family: "Open Sans", Arial, sans-serif;
  }
  .canvas { position: relative; width: 1200px; height: 864px; }
  .card {
    position: absolute;
    width: 540px; height: 308px;
    background: var(--card-black);
    border: 1px solid var(--card-edge);
    box-shadow: 0 10px 28px rgba(0,0,0,.28);
  }
  /* Rear card */
  .card-rear { left: 50px; top: 120px; }
  .rear-brand {
    position: absolute; left: 0; right: 0; top: 70px;
    display: flex; justify-content: center; align-items: center; gap: 14px;
  }
  .rear-brand-mark { width: 22px; height: 22px; background: var(--name-grey); }
  .rear-brand-name {
    font-weight: 800; font-size: 44px; letter-spacing: 2px;
    color: var(--name-grey);
  }
  .rear-services {
    position: absolute; left: 0; right: 0; top: 160px;
    text-align: center; color: var(--text-grey);
    font-size: 17px; line-height: 26px;
  }
  .sep { color: var(--brand-red); font-weight: 700; padding: 0 5px; }
  /* Front card */
  .card-front { left: 610px; top: 436px; }
  .front-brand {
    position: absolute; left: 40px; top: 128px;
    display: flex; align-items: center; gap: 9px;
  }
  .front-brand-mark { width: 16px; height: 16px; background: var(--brand-red); }
  .front-brand-name {
    font-weight: 800; font-size: 21px; color: var(--brand-red); letter-spacing: 1px;
  }
  .divider {
    position: absolute; left: 232px; top: 86px;
    width: 1px; height: 136px; background: var(--rule-grey);
  }
  .contact { position: absolute; left: 256px; top: 96px; }
  .contact-name {
    font-weight: 700; font-size: 21px; color: var(--brand-red); line-height: 24px;
  }
  .contact-title {
    font-size: 15px; color: var(--text-white); letter-spacing: .5px; margin-bottom: 8px;
  }
  .contact-line {
    display: flex; align-items: center; gap: 8px;
    font-size: 15px; color: var(--text-white); line-height: 22px;
  }
  .contact-line svg { width: 12px; height: 12px; flex: none; }
</style>
</head>
<body>
<div class="canvas">

  <section class="card card-rear" aria-label="Card rear">
    <div class="rear-brand">
      <span class="rear-brand-mark"></span>
      <span class="rear-brand-name">GIRDERLINE</span>
    </div>
    <p class="rear-services">
      Pipelines<span class="sep">•</span>Ports<span class="sep">•</span>Utilities<span class="sep">•</span>Forestry<br>
      Power<span class="sep">•</span>Northbridge<span class="sep">•</span>Alder Falls<span class="sep">•</span>Kestrel Bay<br>
      Pinehaven<span class="sep">•</span>Stonemere
    </p>
  </section>

  <section class="card card-front" aria-label="Card front">
    <div class="front-brand">
      <span class="front-brand-mark"></span>
      <span class="front-brand-name">GIRDERLINE</span>
    </div>
    <div class="divider"></div>
    <div class="contact">
      <div class="contact-name">MARA KESSLER</div>
      <div class="contact-title">PRESIDENT</div>
      <div class="contact-line">
        <svg viewBox="0 0 12 12" aria-hidden="true"><path fill="#e0202c" d="M2 1h2.5l1 3-1.5 1a7 7 0 0 0 3 3l1-1.5 3 1V10a1.5 1.5 0 0 1-1.5 1.5A9.5 9.5 0 0 1 .5 2.5 1.5 1.5 0 0 1 2 1z"/></svg>
        <span>555 0142 7781</span>
      </div>
      <div class="contact-line">
        <svg viewBox="0 0 12 12" aria-hidden="true"><rect x="0.5" y="2" width="11" height="8" rx="1" fill="#e0202c"/><path d="M1 2.8 6 6.5l5-3.7" stroke="#161616" stroke-width="1" fill="none"/></svg>
        <span>mara@girderline.com</span>
      </div>
      <div class="contact-line">
        <svg viewBox="0 0 12 12" aria-hidden="true"><circle cx="6" cy="6" r="5.5" fill="#e0202c"/><path d="M.5 6h11M6 .5c-2.5 3-2.5 8 0 11M6 .5c2.5 3 2.5 8 0 11" stroke="#161616" stroke-width=".8" fill="none"/></svg>
        <span>www.girderline.com</span>
      </div>
    </div>
  </section>

</div>
</body>
</html>
```